BrimFalcon Business Cards

We have a defined brand. Please visit our website to get a feel for the product and the color pallets. www.brimfalcon-example.com

We need an updated, world class business card design. (See the attached existing card design). Please utilize BOTH sides of the card as shown and be creative with the layout. I do want the horse head icon to be positioned as it is with the existing card.

The remainder of the layout can be customized and I also want it vertically oriented.

Attached are the logo files and please use the colors as follows:
Green - #A5CE39
Tan - #CDBD99
Black

Feel free to play with the colors.

```html
<!DOCTYPE html>
<html lang="en">
<head>
<meta charset="utf-8">
<title>BrimFalcon Labs Business Card</title>
<link rel="stylesheet" href="https://fonts.googleapis.com/css2?family=Poppins:wght@400;500;700&display=swap">
<style>
  :root {
    --green: #a5ce39;
    --green-deep: #8fb82c;
    --ink: #111111;
    --paper: #ffffff;
    --backdrop: #3a3f46;
  }
  * { margin: 0; padding: 0; box-sizing: border-box; }
  html, body { width: 1200px; height: 900px; overflow: hidden; }
  body {
    background: var(--backdrop);
    font-family: "Poppins", sans-serif;
    display: flex;
    align-items: center;
    justify-content: center;
    gap: 90px;
  }
  .card {
    width: 380px;
    height: 620px;
    border-radius: 18px;
    overflow: hidden;
    position: relative;
    box-shadow: 0 18px 40px rgba(0,0,0,.35);
  }

  /* Front */
  .card-front { background: var(--paper); display: flex; flex-direction: column; }
  .front-body { flex: 1; display: flex; flex-direction: column; align-items: center; padding-top: 58px; }
  .brand-mark { display: flex; align-items: center; gap: 12px; height: 170px; }
  .brand-mark .dot { width: 22px; height: 22px; border-radius: 50%; background: var(--ink); flex: none; }
  .brand-mark .name { font-weight: 700; font-size: 38px; color: var(--ink); letter-spacing: .5px; white-space: nowrap; }
  .person-name { font-weight: 700; font-size: 26px; color: var(--ink); margin-top: 20px; line-height: 1.1; }
  .person-title { font-weight: 400; font-size: 20px; color: var(--green); line-height: 1.3; }
  .rule { width: 110px; height: 2px; background: var(--ink); margin: 14px 0 16px; }
  .contact-icons { display: flex; gap: 10px; margin-bottom: 10px; }
  .contact-icons .icon { width: 30px; height: 30px; border-radius: 50%; background: var(--green); display: flex; align-items: center; justify-content: center; }
  .contact-icons svg { width: 16px; height: 16px; }
  .contact-list { list-style: none; text-align: center; font-size: 16px; color: var(--ink); line-height: 1.55; }
  .contact-list .rule { margin: 12px auto 14px; }
  .pin { width: 22px; height: 28px; margin-top: 10px; margin-bottom: 12px; }
  .front-band {
    height: 140px;
    background: var(--green);
    color: var(--paper);
    display: flex; flex-direction: column; align-items: center; justify-content: center;
    font-size: 22px; font-weight: 500; line-height: 1.3; text-align: center;
  }

  /* Back */
  .card-back {
    background: var(--green);
    display: flex; align-items: center; justify-content: center;
    padding: 0 28px;
  }
  .back-texture { position: absolute; inset: 0; background: radial-gradient(circle at 50% 50%, var(--green) 0%, var(--green-deep) 120%); }
  .back-brand { position: relative; display: flex; align-items: center; gap: 12px; max-width: 100%; }
  .back-brand .dot { width: 22px; height: 22px; border-radius: 50%; background: var(--ink); flex: none; }
  .back-brand .name { font-weight: 700; font-size: 28px; color: var(--ink); white-space: nowrap; }
</style>
</head>
<body>
  <article class="card card-front">
    <div class="front-body">
      <div class="brand-mark">
        <span class="dot"></span>
        <span class="name">BrimFalcon</span>
      </div>
      <h1 class="person-name">Dale Morrow</h1>
      <p class="person-title">President &amp; CEO</p>
      <div class="rule"></div>
      <div class="contact-icons">
        <span class="icon"><svg viewBox="0 0 24 24"><path fill="#fff" d="M6.6 10.8a15 15 0 0 0 6.6 6.6l2.2-2.2c.3-.3.7-.4 1-.2 1.1.4 2.3.6 3.6.6.6 0 1 .4 1 1V20c0 .6-.4 1-1 1A17 17 0 0 1 3 4c0-.6.4-1 1-1h3.5c.6 0 1 .4 1 1 0 1.3.2 2.5.6 3.6.1.3 0 .7-.2 1z"/></svg></span>
        <span class="icon"><svg viewBox="0 0 24 24"><path fill="#fff" d="M3 5h18v14H3z"/><path fill="none" stroke="#a5ce39" stroke-width="2" d="M3 6l9 7 9-7"/></svg></span>
        <span class="icon"><svg viewBox="0 0 24 24"><circle cx="12" cy="12" r="9" fill="none" stroke="#fff" stroke-width="2"/><path fill="none" stroke="#fff" stroke-width="1.6" d="M3 12h18M12 3c3 3 3 15 0 18M12 3c-3 3-3 15 0 18"/></svg></span>
      </div>
      <ul class="contact-list">
        <li>306.555.0148</li>
        <li>dale@brimfalcon-example.com</li>
        <li>www.brimfalconlabs-example.com</li>
        <li><div class="rule"></div></li>
      </ul>
      <svg class="pin" viewBox="0 0 22 28"><path fill="#111" d="M11 0a11 11 0 0 0-11 11c0 8 11 17 11 17s11-9 11-17A11 11 0 0 0 11 0z"/><circle cx="11" cy="11" r="4" fill="#fff"/></svg>
    </div>
    <footer class="front-band">
      <span>Brookvale, Saskatchewan</span>
      <span>Canada</span>
    </footer>
  </article>

  <article class="card card-back">
    <div class="back-texture" role="img" aria-label="Faint repeating brand-symbol pattern in lighter green"></div>
    <div class="back-brand">
      <span class="dot"></span>
      <span class="name">BrimFalcon Labs</span>
    </div>
  </article>
</body>
</html>
```